Redesign of business card for Cedar Ridge Mechanical

We are looking for a new design for our business cards for Cedar Ridge Mechanical. We are a plumbing & HVAC construction company, operating on the West Coast of Canada and USA. Logo attached.
Industry/Entity Type
Construction - Plumbing & HVAC
Contact Information for Business Card
Name, address, phone numbers, email, website address
Look and feel
Each slider illustrates characteristics of the customer's brand and the style your logo design should communicate.

```html
<!DOCTYPE html>
<html lang="en">
<head>
<meta charset="utf-8">
<title>Cedar Ridge Mechanical – Business Card</title>
<link rel="stylesheet" href="https://fonts.googleapis.com/css2?family=Open+Sans:wght@400;700&display=swap">
<style>
  :root {
    --bg: #d4d4d4;
    --ink: #000000;
    --paper: #ffffff;
    --accent-grey: #8e8e8e;
    --shadow: rgba(0,0,0,0.28);
  }
  * { margin: 0; padding: 0; box-sizing: border-box; }
  html, body { width: 1200px; height: 896px; overflow: hidden; }
  body {
    background: var(--bg);
    font-family: "Open Sans", Arial, sans-serif;
    position: relative;
  }
  .card {
    position: absolute;
    left: 334px;
    width: 528px;
    height: 301px;
    border-radius: 24px;
    overflow: hidden;
    box-shadow: 0 14px 22px var(--shadow);
  }
  .card--front { top: 126px; background: var(--ink); }
  .card--back  { top: 475px; background: var(--paper); }

  .wordmark {
    position: absolute;
    display: flex;
    align-items: center;
    gap: 12px;
    font-weight: 700;
    text-transform: uppercase;
    letter-spacing: 0.04em;
    line-height: 1.1;
  }
  .wordmark__square { display: block; flex: none; }
  .card--front .wordmark {
    left: 0; right: 0; top: 0; bottom: 0;
    justify-content: center;
    color: var(--paper);
    font-size: 30px;
  }
  .card--front .wordmark__square {
    width: 30px; height: 30px;
    background: var(--paper);
  }
  .card--back .wordmark {
    left: 20px; top: 22px;
    color: var(--ink);
    font-size: 21px;
  }
  .card--back .wordmark__square {
    width: 22px; height: 22px;
    background: var(--ink);
  }

  .wave { position: absolute; left: 0; top: 0; }

  .contact {
    position: absolute;
    right: 20px;
    top: 116px;
    text-align: right;
    color: var(--paper);
  }
  .contact__name { font-size: 17.5px; font-weight: 700; letter-spacing: 0.02em; line-height: 22px; }
  .contact__role { font-size: 14px; line-height: 18px; }
  .contact__address { font-size: 13px; line-height: 19px; margin-top: 15px; }
  .contact__lines { margin-top: 13px; font-size: 12.5px; line-height: 19px; list-style: none; }
  .contact__lines li { display: flex; justify-content: flex-end; align-items: center; gap: 6px; }
  .contact__lines svg { width: 12px; height: 12px; flex: none; }
</style>
</head>
<body>

<section class="card card--front">
  <div class="wordmark">
    <span class="wordmark__square"></span>
    <span>Cedar Ridge<br>Mechanical</span>
  </div>
</section>

<section class="card card--back">
  <div class="wordmark">
    <span class="wordmark__square"></span>
    <span>Cedar Ridge<br>Mechanical</span>
  </div>

  <svg class="wave" width="528" height="301" viewBox="0 0 528 301" aria-hidden="true">
    <path d="M0,228 C150,280 290,170 360,128 C420,92 480,72 528,92 L528,100 C480,82 420,100 362,138 C292,184 150,292 0,238 Z" fill="var(--accent-grey)"/>
    <path d="M0,235 C150,290 295,184 362,140 C420,104 480,86 528,108 L528,301 L0,301 Z" fill="var(--ink)"/>
  </svg>

  <div class="contact">
    <div class="contact__name">DANIEL HART</div>
    <div class="contact__role">Managing Director</div>
    <div class="contact__address">Your address, City<br>State, Zip 1234</div>
    <ul class="contact__lines">
      <li>123 456 789
        <svg viewBox="0 0 24 24"><path fill="#fff" d="M6.6 10.8a15 15 0 0 0 6.6 6.6l2.2-2.2a1 1 0 0 1 1-.25 11.4 11.4 0 0 0 3.6.57 1 1 0 0 1 1 1V20a1 1 0 0 1-1 1A17 17 0 0 1 3 4a1 1 0 0 1 1-1h3.5a1 1 0 0 1 1 1c0 1.25.2 2.45.57 3.57a1 1 0 0 1-.25 1Z"/></svg>
      </li>
      <li>info@yourmail.com
        <svg viewBox="0 0 24 24"><rect x="2" y="5" width="20" height="14" rx="1.5" fill="#fff"/><path d="M3 6l9 7 9-7" fill="none" stroke="#000" stroke-width="1.8"/></svg>
      </li>
      <li>www.yourwebsite.com
        <svg viewBox="0 0 24 24"><circle cx="12" cy="12" r="10" fill="#fff"/><path d="M2 12h20M12 2c3 3 3 17 0 20M12 2c-3 3-3 17 0 20" fill="none" stroke="#000" stroke-width="1.5"/></svg>
      </li>
    </ul>
  </div>
</section>

</body>
</html>
```